Business Card Design

We are a commercial real estate brokerage in San Francisco, leasing office buildings downtown.
I would like a clean, elegant look. Simple but powerful .

Industry/Entity Type

Business

Contact Information for Business Card

Derek Holloway
lic# 07258143
415.555.0172
derek@velt-commercial.example
velt-commercial.example

```html
<!DOCTYPE html>
<html lang="en">
<head>
<meta charset="utf-8">
<title>Velt Commercial – Business Card</title>
<link rel="stylesheet" href="https://fonts.googleapis.com/css2?family=Lato:wght@400;700&display=swap">
<style>
  :root {
    --page-bg: #eceae7;
    --card-white: #ffffff;
    --slate-blue: #7589a6;
    --charcoal: #4d4d4f;
    --skyline-light: #d9d9d9;
    --skyline-dark: #6a6a6a;
    --text-on-blue: #ffffff;
    --card-shadow: 0 6px 22px rgba(0, 0, 0, 0.18);
  }
  * { margin: 0; padding: 0; box-sizing: border-box; }
  html, body {
    width: 1200px;
    height: 900px;
    overflow: hidden;
    background: var(--page-bg);
    font-family: "Lato", sans-serif;
  }
  .canvas { position: relative; width: 1200px; height: 900px; }

  .card {
    position: absolute;
    width: 556px;
    height: 345px;
    overflow: hidden;
    box-shadow: var(--card-shadow);
  }

  /* Front card */
  .card--front { left: 238px; top: 60px; background: var(--slate-blue); }
  .card__artwork {
    position: absolute;
    left: 0; top: 0;
    width: 250px; height: 100%;
    background: linear-gradient(160deg, var(--skyline-light) 0%, #a9a9a9 45%, var(--skyline-dark) 100%);
  }
  .card__details { position: absolute; left: 282px; top: 42px; color: var(--text-on-blue); }
  .brand-name {
    font-weight: 700;
    line-height: 1;
    letter-spacing: 0.5px;
  }
  .brand-name__top { display: block; font-size: 54px; }
  .brand-name__bottom { display: block; font-size: 23px; margin-top: 4px; }
  .card--front .brand-name { color: var(--text-on-blue); }

  .agent-name { font-size: 18px; font-weight: 700; margin-top: 34px; }
  .agent-licence { font-size: 14px; margin-top: 10px; }
  .contact-list { list-style: none; margin-top: 26px; }
  .contact-list li {
    display: flex; align-items: center;
    font-size: 14.5px; height: 20px;
  }
  .contact-list svg { width: 12px; height: 12px; margin-right: 12px; fill: var(--text-on-blue); }

  /* Back card */
  .card--back { left: 457px; top: 517px; width: 560px; background: var(--card-white); }
  .logo-lockup {
    position: absolute; left: 0; top: 0; width: 100%; height: 100%;
    display: flex; align-items: center; justify-content: center; gap: 18px;
  }
  .logo-lockup__square { width: 40px; height: 40px; background: var(--charcoal); }
  .logo-lockup__divider { width: 2px; height: 120px; background: var(--charcoal); }
  .card--back .brand-name { color: var(--slate-blue); }
  .card--back .brand-name__top { font-size: 64px; }
  .card--back .brand-name__bottom { font-size: 28px; margin-top: 6px; }
</style>
</head>
<body>
<main class="canvas">

  <section class="card card--front" aria-label="Business card front">
    <div class="card__artwork" role="img" aria-label="Grey downtown skyline artwork of office towers"></div>
    <div class="card__details">
      <h1 class="brand-name">
        <span class="brand-name__top">VELT</span>
        <span class="brand-name__bottom">COMMERCIAL</span>
      </h1>
      <p class="agent-name">Derek Holloway</p>
      <p class="agent-licence">Lic# 07258143</p>
      <ul class="contact-list">
        <li>
          <svg viewBox="0 0 24 24" aria-hidden="true"><path d="M6.6 10.8a15.1 15.1 0 0 0 6.6 6.6l2.2-2.2a1 1 0 0 1 1-.25 11.4 11.4 0 0 0 3.6.57 1 1 0 0 1 1 1V20a1 1 0 0 1-1 1A17 17 0 0 1 3 4a1 1 0 0 1 1-1h3.5a1 1 0 0 1 1 1c0 1.25.2 2.45.57 3.57a1 1 0 0 1-.25 1z"/></svg>
          415.555.0172
        </li>
        <li>
          <svg viewBox="0 0 24 24" aria-hidden="true"><path d="M2 5h20v14H2z M3.5 6.5 12 13l8.5-6.5" stroke="#7589a6" stroke-width="1.6"/></svg>
          derek@velt-commercial.example
        </li>
        <li>
          <svg viewBox="0 0 24 24" aria-hidden="true"><path d="M12 2a10 10 0 1 0 0 20 10 10 0 0 0 0-20zm0 2c1.2 1.4 2 3.5 2.2 7H9.8c.2-3.5 1-5.6 2.2-7zM4.1 11a8 8 0 0 1 4.2-6.1A14 14 0 0 0 7.8 11zm0 2h3.7c.1 2.4.6 4.5 1.5 6.1A8 8 0 0 1 4.1 13zm5.7 0h4.4c-.2 3.5-1 5.6-2.2 7-1.2-1.4-2-3.5-2.2-7zm6.4 0h3.7a8 8 0 0 1-5.2 6.1c.9-1.6 1.4-3.7 1.5-6.1zm0-2c-.1-2.4-.6-4.5-1.5-6.1A8 8 0 0 1 19.9 11z"/></svg>
          velt-commercial.example
        </li>
      </ul>
    </div>
  </section>

  <section class="card card--back" aria-label="Business card back">
    <div class="logo-lockup">
      <span class="logo-lockup__square" aria-hidden="true"></span>
      <span class="logo-lockup__divider" aria-hidden="true"></span>
      <h2 class="brand-name">
        <span class="brand-name__top">VELT</span>
        <span class="brand-name__bottom">COMMERCIAL</span>
      </h2>
    </div>
  </section>

</main>
</body>
</html>
```